Business Card for Professional Photographer

I'm looking for an eye catching modern clean design that compliments my logo/ website fonts & colours.
I specialise in architecture, corporate & commercial photography so I'm marketing to professional clients rather than portrait / wedding clients.

I would prefer to not have a solid black design.

My logo brand guide is as follows :

Main front font. : Reislust
Main font colour : #fff
Slogan front font : Ubuntu Bold
Monogram front font : Venti Medium
Container colour : #fff

I need print ready files in pdf .png & .eps formats.

Included in the files below are some screen grabs as reference to font & colours etc.

```html
<!DOCTYPE html>
<html lang="en">
<head>
<meta charset="utf-8">
<title>Northlight Studio – Business Card</title>
<link rel="stylesheet" href="https://fonts.googleapis.com/css2?family=Josefin+Sans:wght@300&family=Open+Sans:wght@400&family=Ubuntu:wght@700&display=swap">
<style>
  :root {
    --backdrop: #5e5e5e;
    --card: #333335;
    --white: #ffffff;
    --gold-text: #d9a54a;
  }
  * { margin: 0; padding: 0; box-sizing: border-box; }
  html, body { width: 1200px; height: 714px; overflow: hidden; }
  body { background: var(--backdrop); position: relative; }

  .card {
    position: absolute;
    top: 240px;
    width: 410px;
    height: 235px;
    background: var(--card);
    overflow: hidden;
  }
  .card--front { left: 188px; }
  .card--back  { left: 604px; }

  .brand {
    position: absolute;
    top: 40px;
    left: 21px;
  }
  .brand__name {
    font-family: "Josefin Sans", sans-serif;
    font-weight: 300;
    font-size: 13px;
    letter-spacing: 2px;
    color: var(--white);
    line-height: 1;
  }
  .brand__tagline {
    margin-top: 5px;
    font-family: "Ubuntu", sans-serif;
    font-weight: 700;
    font-size: 5px;
    letter-spacing: 1.2px;
    color: var(--gold-text);
  }

  .person { position: absolute; left: 21px; top: 107px; }
  .person__name {
    font-family: "Ubuntu", sans-serif;
    font-weight: 700;
    font-size: 16px;
    color: var(--gold-text);
  }
  .person__role {
    font-family: "Open Sans", sans-serif;
    font-size: 11px;
    color: var(--white);
    margin-top: 1px;
  }

  .contact {
    position: absolute; left: 21px; top: 167px;
    list-style: none;
    font-family: "Open Sans", sans-serif;
    font-size: 11px;
    color: var(--white);
    line-height: 15px;
  }
  .contact li { display: flex; align-items: center; gap: 3px; }
  .contact svg { width: 9px; height: 9px; flex: none; }

  .wordmark {
    position: absolute;
    right: 19px;
    top: 170px;
    text-align: right;
  }
  .wordmark__name {
    font-family: "Josefin Sans", sans-serif;
    font-weight: 300;
    font-size: 20px;
    letter-spacing: 2.6px;
    color: var(--white);
    line-height: 1;
    margin-right: -2.6px;
  }
  .wordmark__tagline {
    margin-top: 7px;
    font-family: "Ubuntu", sans-serif;
    font-weight: 700;
    font-size: 7.5px;
    letter-spacing: 2.4px;
    color: var(--gold-text);
    margin-right: -2.4px;
  }
</style>
</head>
<body>
  <section class="card card--front">
    <div class="brand">
      <p class="brand__name">NORTHLIGHT STUDIO</p>
      <p class="brand__tagline">Property Business Products</p>
    </div>

    <div class="person">
      <p class="person__name">DANIEL REYES</p>
      <p class="person__role">Director</p>
    </div>

    <ul class="contact">
      <li>
        <svg viewBox="0 0 10 10" aria-hidden="true"><path d="M2 1 L4 1 L4.6 3 L3.4 3.8 Q4.4 5.8 6.2 6.6 L7 5.4 L9 6 L9 8 Q5 9 2 6 Q0.8 4 2 1Z" fill="#d9a54a"/></svg>
        555 018 2047
      </li>
      <li>
        <svg viewBox="0 0 10 10" aria-hidden="true"><rect x="0.5" y="2" width="9" height="6" fill="#d9a54a"/><path d="M0.5 2 L5 5.5 L9.5 2" fill="none" stroke="#333335" stroke-width="0.8"/></svg>
        info@northlightstudio.com
      </li>
      <li>
        <svg viewBox="0 0 10 10" aria-hidden="true"><circle cx="5" cy="5" r="4.3" fill="#d9a54a"/><path d="M0.8 5 H9.2 M5 0.8 Q2.5 5 5 9.2 M5 0.8 Q7.5 5 5 9.2" fill="none" stroke="#333335" stroke-width="0.7"/></svg>
        www.northlightstudio.com
      </li>
    </ul>
  </section>

  <section class="card card--back">
    <div class="wordmark">
      <p class="wordmark__name">NORTHLIGHT STUDIO</p>
      <p class="wordmark__tagline">Property Business Products</p>
    </div>
  </section>
</body>
</html>
```